Tide & Thistle Website Creation For Online Spirits Sales via MerrowVats.com

Want a Website developed that I will use to partner with Merrow Vats to sell my signature rum online. Merrow Vats will add the final code to make the website an e-commerce site. Website should have links to Social media pages, recipies, About, news and events, products. I have he domain name already just need a designer to make the website look professional. Need website capable of being viewed on iPhone and Android devices. Please use the color scheme that is on the label. The brand motto is: Celebrate Life With Family old and new friends. The bottle sent in the images will be replaced with and actual high resolution image of the bottle when it is produce on 27 DEC 21. Can give the selected designer access to develop the website. I have the hostbramble.com domain name. Final code will be added by a designer from MerrowVats.com to make it a e-commerce store.
Updates

I added more information to refine the design I wanted. I should have had this information available to the designers when I started the project.

Target Market(s)

Target Market is 25-50 year old who drink rum

Industry/Entity Type

Spirits. Using Website to sell Rum online

Number of Pages Required

1 page

Font styles to use
Sans Serif

Colors
00AB8E
00BBA5
67D7C9
C6EFE9
E9F9F6

Requirements
Must have
• Must look elegant and of high class. Rum is being market as a premium unnamed rum.
Nice to have
• Video of people drinking, smiling and celebrating

```html
<!DOCTYPE html>
<html lang="en">
<head>
<meta charset="utf-8">
<title>Tide &amp; Thistle — Celebrate Life</title>
<link rel="stylesheet" href="https://fonts.googleapis.com/css2?family=Noticia+Text:wght@400;700&family=Nunito+Sans:wght@400;600;700&display=swap">
<style>
  :root {
    --teal: #1aa48a;
    --teal-deep: #179c7d;
    --teal-ink: #1e9e86;
    --cream: #f1f0e0;
    --ink: #2b2b2b;
    --muted: #3c3c3c;
    --white: #ffffff;
    --black: #000000;
  }
  * { margin: 0; padding: 0; box-sizing: border-box; }
  html, body { width: 1200px; height: 2874px; overflow: hidden; background: var(--white); }
  body { position: relative; font-family: "Nunito Sans", Arial, sans-serif; color: var(--ink); }
  .abs { position: absolute; }
  .serif { font-family: "Noticia Text", Georgia, serif; }

  /* Header */
  .site-header { position: absolute; left: 0; top: 0; width: 1200px; height: 65px; background: var(--white); z-index: 5; }
  .brand-tab { position: absolute; left: 111px; top: 0; width: 203px; height: 97px; background: var(--white); border-radius: 0 0 40px 40px; z-index: 6; text-align: center; }
  .brand-dot { display: block; width: 46px; height: 46px; border-radius: 50%; background: var(--black); margin: 8px auto 0; }
  .brand-name { font-family: "Noticia Text", Georgia, serif; font-size: 22px; color: var(--black); letter-spacing: 0.5px; margin-top: 4px; }
  .main-nav { position: absolute; left: 496px; top: 20px; display: flex; gap: 24px; font-family: "Noticia Text", Georgia, serif; font-size: 17px; color: var(--ink); }
  .main-nav .active { color: var(--teal); font-weight: 700; }
  .btn { display: inline-flex; align-items: center; justify-content: center; border-radius: 26px; font-weight: 700; font-size: 17px; color: var(--white); background: var(--teal); }
  .btn-outline { background: transparent; border: 2px solid var(--teal); }
  .header-cta { position: absolute; left: 964px; top: 13px; width: 122px; height: 40px; }

  /* Hero */
  .hero { position: absolute; left: 0; top: 65px; width: 1200px; height: 605px; overflow: hidden; }
  .hero-photo { position: absolute; inset: 0; background: radial-gradient(ellipse at 50% 40%, #6a5a4c 0%, #3f3530 45%, #221d1c 100%); }
  .hero-curve { position: absolute; left: 0; top: 0; }
  .hero-title { position: absolute; left: 300px; top: 182px; width: 600px; text-align: center; font-family: "Noticia Text", Georgia, serif; font-weight: 700; font-size: 41px; line-height: 52px; color: var(--white); text-transform: uppercase; }
  .hero-cta-1 { position: absolute; left: 468px; top: 371px; width: 127px; height: 45px; }
  .hero-cta-2 { position: absolute; left: 605px; top: 371px; width: 126px; height: 45px; }
  .hero-arrow { position: absolute; top: 269px; }
  .cheers { position: absolute; left: 0; width: 1200px; top: 527px; text-align: center; color: var(--white); font-size: 16px; letter-spacing: 1px; }

  /* About */
  .about-media { position: absolute; left: 129px; top: 752px; }
  .about-title { position: absolute; left: 605px; top: 792px; font-family: "Noticia Text", Georgia, serif; font-size: 37px; color: var(--teal); }
  .rule { position: absolute; height: 2px; width: 60px; background: var(--ink); }
  .about-text { position: absolute; left: 605px; top: 862px; width: 470px; font-size: 17px; line-height: 30px; color: var(--muted); }
  .about-cta { position: absolute; left: 603px; top: 1031px; width: 127px; height: 45px; }

  /* Solutions */
  .solutions { position: absolute; left: 0; top: 1222px; width: 1200px; height: 731px; background: var(--teal-deep); }
  .section-title { position: absolute; left: 0; width: 1200px; text-align: center; font-family: "Noticia Text", Georgia, serif; font-size: 37px; }
  .solutions .section-title { top: 50px; color: var(--white); }
  .bottle { position: absolute; left: 507px; top: 188px; width: 160px; height: 461px; border-radius: 30px 30px 40px 40px; background: linear-gradient(180deg, #e9e4d6 0%, #e9e4d6 18%, #b9772b 32%, #a0601f 60%, #d7d3c2 75%, #b46f26 100%); }
  .feature-icon { position: absolute; width: 78px; height: 78px; border-radius: 50%; background: var(--cream); }
  .feature { position: absolute; width: 260px; color: var(--white); }
  .feature h3 { font-family: "Noticia Text", Georgia, serif; font-weight: 400; font-size: 25px; line-height: 30px; margin-bottom: 4px; }
  .feature p { font-size: 17px; line-height: 30px; }
  .feature.left { text-align: right; }

  /* Reviews */
  .reviews .section-title { top: 2034px; color: var(--teal); }
  .avatar { position: absolute; left: 546px; top: 2146px; width: 106px; height: 106px; border-radius: 50%; border: 3px solid var(--teal); background: var(--white); }
  .avatar span { position: absolute; inset: 6px; border-radius: 50%; background: linear-gradient(160deg, #9fb7c0 0%, #a88468 60%, #7d6a4a 100%); }
  .quote { position: absolute; left: 230px; top: 2276px; width: 740px; text-align: center; font-size: 17px; line-height: 30px; color: var(--muted); }
  .author { position: absolute; left: 0; width: 1200px; top: 2388px; text-align: center; font-size: 19px; font-weight: 600; color: var(--ink); }
  .dot { position: absolute; top: 2447px; width: 11px; height: 11px; border-radius: 50%; background: var(--teal); }
  .dot.current { width: 16px; height: 16px; top: 2445px; background: #1c5d52; border: 2px solid var(--teal); }

  /* Footer */
  .site-footer { position: absolute; left: 0; top: 2540px; width: 1200px; height: 334px; }
  .social { position: absolute; top: 92px; width: 32px; height: 32px; border-radius: 50%; border: 1.5px solid var(--white); }
  .footer-nav { position: absolute; left: 0; width: 1200px; top: 144px; display: flex; justify-content: center; gap: 25px; font-family: "Noticia Text", Georgia, serif; font-size: 17px; color: var(--white); }
  .footer-nav .active { font-weight: 700; }
  .footer-line { position: absolute; left: 0; width: 1200px; text-align: center; color: var(--white); font-size: 16px; display: flex; justify-content: center; align-items: center; gap: 10px; }
</style>
</head>
<body>

<header class="site-header">
  <div class="brand-tab">
    <span class="brand-dot"></span>
    <div class="brand-name">TIDE &amp; THISTLE</div>
  </div>
  <nav class="main-nav">
    <span class="active">Home</span><span>Recipes</span><span>About</span><span>News &amp; Events</span><span>Products</span>
  </nav>
  <span class="btn header-cta">Contact us</span>
</header>

<section class="hero">
  <div class="hero-photo" role="img" aria-label="Friends raising glasses together in a toast at a dinner table"></div>
  <div class="hero-photo" style="background:rgba(20,16,14,0.25)"></div>
  <svg class="hero-curve" width="1200" height="605" viewBox="0 0 1200 605" aria-hidden="true">
    <path d="M0 526 Q600 685 1200 526 L1200 605 L0 605 Z" fill="#ffffff"/>
  </svg>
  <h1 class="hero-title">Celebrate life with family, old and new friends</h1>
  <span class="btn hero-cta-1">Contact us</span>
  <span class="btn btn-outline hero-cta-2">Learn More</span>
  <svg class="hero-arrow" style="left:30px" width="44" height="44" viewBox="0 0 44 44" aria-hidden="true">
    <circle cx="22" cy="22" r="20" fill="none" stroke="#ffffff" stroke-opacity="0.6" stroke-width="2"/>
    <path d="M31 22 H13 M20 15 L13 22 L20 29" fill="none" stroke="#ffffff" stroke-opacity="0.6" stroke-width="2.5"/>
  </svg>
  <svg class="hero-arrow" style="left:1123px" width="44" height="44" viewBox="0 0 44 44" aria-hidden="true">
    <circle cx="22" cy="22" r="20" fill="none" stroke="#ffffff" stroke-width="2"/>
    <path d="M13 22 H31 M24 15 L31 22 L24 29" fill="none" stroke="#ffffff" stroke-width="2.5"/>
  </svg>
  <div class="cheers">CHEERS
    <svg style="display:block;margin:6px auto 0" width="16" height="30" viewBox="0 0 16 30" aria-hidden="true">
      <path d="M8 0 V28 M1 21 L8 28 L15 21" fill="none" stroke="#ffffff" stroke-width="1.6"/>
    </svg>
  </div>
</section>

<section class="about">
  <svg class="about-media" width="374" height="374" viewBox="0 0 374 374">
    <circle cx="187" cy="187" r="184" fill="#e6e4d2"/>
    <circle cx="187" cy="187" r="164" fill="#1b120e"/>
    <defs>
      <radialGradient id="whiskyGlow" cx="45%" cy="45%" r="60%">
        <stop offset="0%" stop-color="#e0893a"/>
        <stop offset="55%" stop-color="#7a3512"/>
        <stop offset="100%" stop-color="#1b120e"/>
      </radialGradient>
    </defs>
    <circle cx="187" cy="187" r="164" fill="url(#whiskyGlow)" role="img" aria-label="Glasses of rum on ice"/>
    <circle cx="187" cy="187" r="27" fill="none" stroke="#ffffff" stroke-width="4"/>
    <path d="M179 174 L200 187 L179 200 Z" fill="none" stroke="#ffffff" stroke-width="3.5" stroke-linejoin="round"/>
  </svg>
  <h2 class="about-title">About Us</h2>
  <span class="rule" style="left:605px;top:844px"></span>
  <p class="about-text">Sed ut perspiciatis unde omnis iste natus error sit voluptatem accusantium doloremque laudantium, totam rem aperiam, eaque ipsa quae ab illo inventore veritatis et quasi architecto beatae vitae dicta sunt explicabo. Nemo enim ipsam voluptatem quia.</p>
  <span class="btn about-cta">Contact us</span>
</section>

<section class="solutions">
  <h2 class="section-title">Our Solutions</h2>
  <span class="rule" style="left:570px;top:109px;background:#ffffff"></span>
  <div class="bottle" role="img" aria-label="Bottle of Tide &amp; Thistle authentic rum"></div>

  <div class="feature-icon" style="left:407px;top:240px">
    <svg width="78" height="78" viewBox="0 0 78 78" aria-hidden="true"><path d="M26 40 L42 24 L56 24 L56 38 L40 54 Z" fill="none" stroke="#1aa48a" stroke-width="2.5" stroke-linejoin="round"/><circle cx="49" cy="31" r="3" fill="none" stroke="#1aa48a" stroke-width="2.5"/></svg>
  </div>
  <div class="feature-icon" style="left:707px;top:240px">
    <svg width="78" height="78" viewBox="0 0 78 78" aria-hidden="true"><rect x="22" y="32" width="34" height="22" fill="none" stroke="#1aa48a" stroke-width="2.5"/><path d="M22 32 L39 45 L56 32 M39 18 V34 M33 24 L39 18 L45 24" fill="none" stroke="#1aa48a" stroke-width="2.5"/></svg>
  </div>
  <div class="feature-icon" style="left:407px;top:454px">
    <svg width="78" height="78" viewBox="0 0 78 78" aria-hidden="true"><path d="M30 48 Q30 30 42 27 Q52 30 52 44 L56 50 L28 54 Z" fill="none" stroke="#1aa48a" stroke-width="2.5" stroke-linejoin="round"/><path d="M38 55 Q42 60 46 54" fill="none" stroke="#1aa48a" stroke-width="2.5"/></svg>
  </div>
  <div class="feature-icon" style="left:707px;top:454px">
    <svg width="78" height="78" viewBox="0 0 78 78" aria-hidden="true"><circle cx="36" cy="37" r="13" fill="none" stroke="#1aa48a" stroke-width="2.5"/><path d="M45 46 L56 57 M29 40 L34 35 L38 39 L44 32" fill="none" stroke="#1aa48a" stroke-width="2.5"/></svg>
  </div>

  <div class="feature left" style="left:110px;top:265px">
    <h3>White-Label</h3>
    <p>Lorem ipsum dolor sit amet, consectetur adipiscing elit, sed do eiusmod tempor incididunt .</p>
  </div>
  <div class="feature" style="left:816px;top:265px">
    <h3>Direct Marketing</h3>
    <p>Lorem ipsum dolor sit amet, consectetur adipiscing elit, sed do eiusmod tempor incididunt .</p>
  </div>
  <div class="feature left" style="left:116px;top:479px">
    <h3>Subscriptions</h3>
    <p>Lorem ipsum dolor sit amet, consectetur adipiscing elit, sed do eiusmod tempor incididunt .</p>
  </div>
  <div class="feature" style="left:816px;top:479px">
    <h3>Analytics Suite</h3>
    <p>Lorem ipsum dolor sit amet, consectetur adipiscing elit, sed do eiusmod tempor incididunt .</p>
  </div>
</section>

<section class="reviews">
  <h2 class="section-title">Client Reviews</h2>
  <span class="rule" style="left:568px;top:2096px"></span>
  <div class="avatar"><span role="img" aria-label="Portrait of a client"></span></div>
  <p class="quote">Nam libero tempore, cum soluta nobis est eligendi optio cumque nihil impedit quo minus id quod maxime placeat facere possimus, omnis voluptas assumenda est, omnis dolor repellendus.</p>
  <p class="author">- Lorem Ipsum</p>
  <span class="dot current" style="left:562px"></span>
  <span class="dot" style="left:591px"></span>
  <span class="dot" style="left:617px"></span>
</section>

<footer class="site-footer">
  <svg class="abs" style="left:0;top:0" width="1200" height="334" viewBox="0 0 1200 334" aria-hidden="true">
    <path d="M0 82 Q600 -40 1200 82 L1200 334 L0 334 Z" fill="#000000"/>
  </svg>
  <span class="social" style="left:539px" aria-label="Social page"></span>
  <span class="social" style="left:584px" aria-label="Social page"></span>
  <span class="social" style="left:628px" aria-label="Social page"></span>
  <nav class="footer-nav">
    <span class="active">Home</span><span>Recipes</span><span>About</span><span>News &amp; Events</span><span>Products</span>
  </nav>
  <div class="footer-line" style="top:185px">
    <svg width="36" height="18" viewBox="0 0 36 18" aria-hidden="true"><rect x="10" y="2" width="24" height="14" fill="none" stroke="#ffffff" stroke-width="1.3"/><path d="M10 2 L22 11 L34 2 M1 6 H7 M3 10 H7 M1 14 H7" fill="none" stroke="#ffffff" stroke-width="1.3"/></svg>
    <span>contact@tidethistle</span>
  </div>
  <div class="footer-line" style="top:228px">
    <svg width="12" height="18" viewBox="0 0 12 18" aria-hidden="true"><rect x="1" y="1" width="10" height="16" rx="1.5" fill="none" stroke="#ffffff" stroke-width="1.4"/></svg>
    <span>(555-014-7720)</span>
  </div>
  <div class="footer-line" style="top:264px">© 2021 Tide &amp; Thistle. All Rights Reserved.</div>
</footer>

</body>
</html>
```